Independent Artist - Album Cover Design

I need a full album cover design for my debut album Velvet Midnight Hours. The album is a love-inspired, passionate, soulful, relationship laden album. An album that can relate to anyone in love (or lust/obsession), going through ups and downs of relationships,and overcoming any hardships and enjoying the joys of true love, sex, and companionship. My first thoughts are a black and white design with the color red poppin off in there maybe in some of the lettering but I am open to some creative ideas. Looking for something clean and sexy that represents what the album is about. I was thinking maybe having a photo of myself on there but don't really have any that would work Just Then but I can take some and send a link if you have some good ideas.

My Artist name if I didnt mention before is Darielle. I would like that on the album cover as well. Also I need a full album cover Front and Back. Below is the track list if you could incorporate that as well. And below is also a link to some photos. Thank you.

https://www.filecradle.example/sh/qm4rtwplkd8vnbh/KexFuromTy

1 .Her Smile (Feat. Marty Quickstep)
2.  Neon Drift (Feat. Rell Vo)
3 .Held The Rain (Feat. Tovo)
4 . Spin Me Slower
5. Sidewayz
6.  With Her (Feat. Rell Vo)
7 .Stars Fall Down For Us
8 . Just Then
9 . Morning Came Late
10.  Past This Gate
11.  We Might
12 . Seasons Of Rapture

New Clearer Pictures Posted to dropbox folder. Thanks.

https://www.filecradle.example/sh/qm4rtwplkd8vnbh/EEPr7h31WkMcTraGuyOpsazx

```html
<!DOCTYPE html>
<html lang="en">
<head>
<meta charset="utf-8">
<title>Darielle – Velvet Midnight Hours – Album Package</title>
<link rel="stylesheet" href="https://fonts.googleapis.com/css2?family=Josefin+Sans:wght@300;400&family=Montserrat:wght@600;700;800&display=swap">
<style>
  :root {
    --page: #ffffff;
    --panel: #050506;
    --text-light: #e9ecef;
    --text-soft: #b9bec4;
    --text-dim: #7b8087;
    --flare-blue: rgba(120,160,255,.9);
  }
  * { margin: 0; padding: 0; box-sizing: border-box; }
  html, body { width: 1200px; height: 750px; overflow: hidden; background: var(--page); }
  .sheet { position: relative; width: 1200px; height: 750px; }

  .panel { position: absolute; background: var(--panel); overflow: hidden; }
  .front { left: 9px; top: 7px; width: 360px; height: 358px; }
  .back { left: 373px; top: 7px; width: 358px; height: 358px; }
  .inlay { left: 735px; top: 7px; width: 452px; height: 358px; }

  .photo { position: absolute; }
  .front .photo {
    inset: 0;
    background:
      radial-gradient(ellipse 40% 30% at 18% 82%, rgba(194,57,26,.75), transparent 70%),
      radial-gradient(ellipse 35% 55% at 45% 35%, rgba(150,150,155,.55), transparent 75%),
      radial-gradient(ellipse 60% 50% at 70% 60%, rgba(92,94,98,.45), transparent 75%),
      var(--panel);
  }
  .back .photo {
    left: 0; top: 0; width: 200px; height: 358px;
    background:
      radial-gradient(ellipse 40% 25% at 15% 70%, rgba(194,57,26,.75), transparent 75%),
      radial-gradient(ellipse 45% 40% at 55% 30%, rgba(140,140,145,.55), transparent 75%),
      radial-gradient(ellipse 60% 55% at 40% 65%, rgba(92,94,98,.4), transparent 75%),
      var(--panel);
  }

  .wordmark {
    position: absolute;
    font-family: "Montserrat", sans-serif;
    font-weight: 800;
    color: var(--text-light);
    letter-spacing: -0.5px;
    line-height: 1;
    white-space: nowrap;
  }
  .front .wordmark { left: 96px; top: 278px; font-size: 40px; }
  .back .wordmark { left: 166px; top: 213px; font-size: 29px; }

  .flare {
    position: absolute; height: 2px;
    background: linear-gradient(90deg, transparent, var(--flare-blue), transparent);
  }
  .front .flare { left: 60px; top: 320px; width: 300px; }
  .back .flare { left: 140px; top: 244px; width: 180px; }

  .album-title {
    position: absolute;
    font-family: "Josefin Sans", sans-serif;
    font-weight: 400;
    color: var(--text-light);
    text-transform: uppercase;
    white-space: nowrap;
  }
  .front .album-title { left: 98px; top: 318px; font-size: 11px; letter-spacing: 3.2px; }

  .tracklist {
    position: absolute; left: 164px; top: 38px;
    list-style: none;
    font-family: "Josefin Sans", sans-serif;
    font-size: 7.2px; letter-spacing: .3px;
    color: var(--text-soft);
    text-transform: uppercase;
    white-space: nowrap;
  }
  .tracklist li { height: 11.7px; display: flex; line-height: 11.7px; }
  .tracklist .no { width: 21px; flex: none; color: var(--text-light); }

  .credits {
    position: absolute;
    font-family: "Josefin Sans", sans-serif;
    font-size: 6px; letter-spacing: .4px; line-height: 8px;
    color: var(--text-dim); text-transform: uppercase;
    white-space: nowrap;
  }
  .credits .head { color: var(--text-soft); }
  .back .credits { left: 166px; top: 258px; }
  .inlay .credits { left: 47px; top: 282px; }

  .links {
    position: absolute; left: 0; top: 330px; width: 358px; height: 8px;
    font-family: "Josefin Sans", sans-serif;
    font-size: 4.6px; letter-spacing: .3px;
    color: var(--text-dim); text-transform: uppercase;
    white-space: nowrap;
  }
  .links span { position: absolute; top: 0; }
  .links .l1 { left: 25px; }
  .links .l2 { left: 133px; }
  .links .l3 { left: 228px; }

  .vertical {
    position: absolute; white-space: nowrap;
    text-transform: uppercase; color: var(--text-light);
  }
  .vertical.title { font-family: "Josefin Sans", sans-serif; font-weight: 300; font-size: 9px; letter-spacing: 1px; }
  .vertical.name { font-family: "Montserrat", sans-serif; font-weight: 700; font-size: 10px; letter-spacing: 1px; }
  .up { transform: rotate(-90deg); transform-origin: left top; }
  .down { transform: rotate(90deg); transform-origin: left top; }
  .inlay .t1 { left: 17px; top: 172px; }
  .inlay .n1 { left: 438px; top: 38px; }
  .inlay .n2 { left: 15px; top: 296px; }
  .inlay .t2 { left: 437px; top: 176px; }

  .disc { position: absolute; left: 13px; top: 378px; width: 362px; height: 362px; }
  .disc svg { display: block; }
</style>
</head>
<body>
<main class="sheet">

  <section class="panel front" aria-label="Front cover">
    <div class="photo" role="img" aria-label="Black and white portrait of the artist in a hat and tank top with tattooed arm, smoke and a red glow"></div>
    <span class="flare"></span>
    <h1 class="wordmark">DARIELLE</h1>
    <p class="album-title">Velvet Midnight Hours</p>
  </section>

  <section class="panel back" aria-label="Back cover">
    <div class="photo" role="img" aria-label="Black and white photo of the artist showing tattooed arm, with a red glow"></div>
    <ol class="tracklist">
      <li><span class="no">01.</span>Her Smile (Feat. Marty Quickstep)</li>
      <li><span class="no">02.</span>Neon Drift (Feat. Rell Vo)</li>
      <li><span class="no">03.</span>Held The Rain (Feat. Tovo)</li>
      <li><span class="no">04.</span>Spin Me Slower</li>
      <li><span class="no">05.</span>Sidewayz</li>
      <li><span class="no">06.</span>With Her (Feat. Rell Vo)</li>
      <li><span class="no">07.</span>Stars Fall Down For Us</li>
      <li><span class="no">08.</span>Just Then (Feat. Rell Vo)</li>
      <li><span class="no">09.</span>Morning Came Late</li>
      <li><span class="no">10.</span>Past This Gate</li>
      <li><span class="no">11.</span>We Might</li>
      <li><span class="no">12.</span>Seasons Of Rapture</li>
    </ol>
    <span class="flare"></span>
    <h2 class="wordmark">DARIELLE</h2>
    <div class="credits">
      <p class="head">Special Thanks</p>
      <p>Producers: Darielle, KR Beats Featured</p>
      <p>Artist: Rell Vo, Marty Quickstep, Tovo 7</p>
    </div>
    <div class="links">
      <span class="l1">www.stagewave.example/darielle</span>
      <span class="l2">www.dariellecarter.example</span>
      <span class="l3">www.tunecrate.example/nightline</span>
    </div>
  </section>

  <section class="panel inlay" aria-label="Inlay tray card">
    <span class="vertical title up t1">Velvet Midnight Hours</span>
    <span class="vertical name down n1">Darielle</span>
    <span class="vertical name up n2">Darielle</span>
    <span class="vertical title down t2">Velvet Midnight Hours</span>
    <div class="credits">
      <p class="head">Special Thanks</p>
      <p>Producers: Darielle, KR Beats Featured</p>
      <p>Artist: Rell Vo, Marty Quickstep, Tovo 7</p>
    </div>
  </section>

  <section class="disc" aria-label="Disc label">
    <svg width="362" height="362" viewBox="0 0 362 362">
      <defs>
        <clipPath id="disc-clip"><circle cx="181" cy="181" r="180"/></clipPath>
        <radialGradient id="disc-glow" cx="0.6" cy="0.7" r="0.6">
          <stop offset="0" stop-color="#1d2b55"/>
          <stop offset="1" stop-color="#07080c"/>
        </radialGradient>
        <path id="rim-left" d="M 40 120 A 152 152 0 0 0 150 330"/>
        <path id="rim-right" d="M 215 330 A 152 152 0 0 0 325 120"/>
        <path id="rim-bottom" d="M 110 342 A 165 165 0 0 0 252 342"/>
      </defs>
      <circle cx="181" cy="181" r="180" fill="#060607"/>
      <rect x="0" y="185" width="283" height="177" fill="url(#disc-glow)" clip-path="url(#disc-clip)" role="img" aria-label="Dark blue glow panel"/>
      <text x="185" y="87" text-anchor="middle" fill="#e9ecef" font-family="Josefin Sans, sans-serif" font-size="11" letter-spacing="3">VELVET MIDNIGHT HOURS</text>
      <line x1="60" y1="288" x2="300" y2="288" stroke="#6f95ff" stroke-opacity=".6" stroke-width="1.5"/>
      <text x="181" y="300" text-anchor="middle" fill="#e9ecef" font-family="Montserrat, sans-serif" font-weight="800" font-size="32">DARIELLE</text>
      <text fill="#8a8f96" font-family="Josefin Sans, sans-serif" font-size="6" letter-spacing=".8"><textPath href="#rim-left">WWW.STAGEWAVE.EXAMPLE/DARIELLE</textPath></text>
      <text fill="#8a8f96" font-family="Josefin Sans, sans-serif" font-size="6" letter-spacing=".8"><textPath href="#rim-bottom" startOffset="50%" text-anchor="middle">WWW.DARIELLECARTER.EXAMPLE</textPath></text>
      <text fill="#8a8f96" font-family="Josefin Sans, sans-serif" font-size="6" letter-spacing=".8"><textPath href="#rim-right">WWW.TUNECRATE.EXAMPLE/NIGHTLINE</textPath></text>
    </svg>
  </section>

</main>
</body>
</html>
```